Rack card for marketing

Office to office marketing for knee pain treatment

Target Market(s)

Medical Offices, Retired patients looking to maintain active lifestlye. Family practice medical offices

Industry/Entity Type

Medical

Colors
0054AA
0677BA
7BADD7
CADEEF
E8F1F8

Requirements
Must have
• Font that matches logo, RMH logo, graphic of a retiree who looks active and happy versus a knee graphic
Nice to have
• The best ever rack card!!! Easy to Read, simplicity is key.

```html
<!DOCTYPE html>
<html lang="en">
<head>
<meta charset="utf-8">
<title>RMH Knee Pain Rack Cards</title>
<link href="https://fonts.googleapis.com/css2?family=Fira+Sans:wght@400;500;600;700;800&family=Oswald:wght@300;400&display=swap" rel="stylesheet">
<style>
  :root {
    --page: #eef1f4;
    --panel: #246590;
    --brand: #2b6a96;
    --wave-white: #ffffff;
    --wave-grey: #a7a2a2;
    --head: #d6dde6;
    --list: #f2f5f8;
    --tick: #d3dae3;
    --sky: #dfe3e6;
    --grass: #6f8a52;
  }
  * { box-sizing: border-box; margin: 0; padding: 0; }
  html, body { width: 1200px; height: 904px; overflow: hidden; }
  body { background: var(--page); font-family: "Fira Sans", sans-serif; position: relative; }

  .rack-card {
    position: absolute; top: 60px; width: 323px; height: 784px;
    background: var(--panel); overflow: hidden;
    box-shadow: 0 4px 14px rgba(0,0,0,.18);
  }
  .rack-card--treatments { left: 252px; }
  .rack-card--procedures { left: 625px; }

  .hero-photo { position: absolute; left: 0; top: 0; width: 323px; height: 400px; }
  .hero-photo--cyclists { background: linear-gradient(180deg, #e2e5e7 0%, #d7dbde 40%, #4d6a86 58%, #6c7f56 80%, var(--grass) 100%); }
  .hero-photo--clinic { background: linear-gradient(180deg, #f4f6f8 0%, #cfdbe7 28%, #6b87a6 42%, #d9d6cf 58%, #a9a49c 78%, #8f8f8f 100%); }

  .brand-name {
    position: absolute; left: 0; right: 0; top: 34px; text-align: center;
    color: var(--brand); font-weight: 600; line-height: 1;
  }
  .brand-name__short { display: block; font-size: 44px; letter-spacing: 1px; }
  .brand-name__long { display: block; font-size: 15px; margin-top: 6px; }

  .wave { position: absolute; left: 0; top: 292px; width: 323px; height: 130px; }

  .panel-heading {
    position: absolute; left: 23px; top: 420px; width: 290px;
    color: var(--head); font-weight: 700; font-size: 18.5px; line-height: 1.25;
  }
  .checklist { position: absolute; left: 23px; list-style: none; }
  .checklist li {
    display: flex; align-items: center; gap: 6px;
    color: var(--list); font-size: 11.6px; font-weight: 500; height: 19.2px;
  }
  .checklist svg { width: 9px; height: 9px; flex: none; }
  .checklist--treatments { top: 480px; }
  .checklist--procedures { top: 462px; }

  .round-photo {
    position: absolute; width: 136px; height: 136px; border-radius: 50%;
    border: 3px solid #b9b6b6;
  }
  .round-photo--knee { left: 168px; top: 564px; background: radial-gradient(circle at 45% 50%, #8a2c2c 0%, #4a3a3a 35%, #9a9a9a 70%, #d8d8d8 100%); }
  .round-photo--doctor { left: 167px; top: 568px; background: linear-gradient(180deg, #c8d6e2 0%, #9fb7c9 45%, #6f8f62 62%, #2f6a9a 100%); }

  .count-heading { position: absolute; left: 22px; top: 412px; display: flex; align-items: center; gap: 6px; }
  .count-heading__number { font-family: "Oswald", sans-serif; font-weight: 400; font-size: 46px; color: var(--tick); line-height: 1; }
  .count-heading__text { color: var(--head); font-weight: 800; font-size: 18.5px; line-height: 1.2; }

  .physician { position: absolute; left: 22px; top: 606px; }
  .physician__name { font-family: "Oswald", sans-serif; font-weight: 300; font-size: 19px; color: var(--head); }
  .physician__role { color: var(--list); font-size: 13px; font-weight: 500; line-height: 1.3; margin-top: 2px; }

  .contact { position: absolute; left: 23px; top: 722px; color: var(--list); }
  .contact__cta { font-weight: 800; font-size: 11.4px; color: #fff; letter-spacing: .1px; }
  .contact__row { display: flex; align-items: center; gap: 9px; font-size: 10.4px; font-weight: 400; margin-top: 5px; }
  .contact__item { display: flex; align-items: center; gap: 3px; }
  .contact__item svg { width: 10px; height: 10px; }
</style>
</head>
<body>

<!-- Treatments card -->
<section class="rack-card rack-card--treatments">
  <div class="hero-photo hero-photo--cyclists" role="img" aria-label="Active retired couple riding bicycles along a grassy coastal path"></div>
  <div class="brand-name"><span class="brand-name__short">RMH</span><span class="brand-name__long">Ridgeline Medical Health</span></div>
  <svg class="wave" viewBox="0 0 323 130" preserveAspectRatio="none" aria-hidden="true">
    <path d="M0,48 C60,34 120,44 190,96 L0,130 Z" fill="var(--panel)"/>
    <path d="M0,86 C70,70 140,92 200,96 C262,100 300,60 323,24 L323,130 L0,130 Z" fill="var(--wave-white)"/>
    <path d="M0,96 C70,84 140,108 205,112 C262,115 300,80 323,44 L323,130 L0,130 Z" fill="var(--wave-grey)"/>
    <path d="M0,104 C70,92 140,98 200,100 C262,100 300,70 323,52 L323,130 L0,130 Z" fill="var(--panel)"/>
  </svg>
  <h2 class="panel-heading">Comprehensive Non-operative Treatment for Knee Pain</h2>
  <ul class="checklist checklist--treatments">
    <li><svg viewBox="0 0 10 10"><circle cx="5" cy="5" r="5" fill="var(--tick)"/><path d="M2.8 5.1 4.4 6.6 7.3 3.6" stroke="var(--panel)" stroke-width="1.4" fill="none"/></svg>Evidence Based Supplementation</li>
    <li><svg viewBox="0 0 10 10"><circle cx="5" cy="5" r="5" fill="var(--tick)"/><path d="M2.8 5.1 4.4 6.6 7.3 3.6" stroke="var(--panel)" stroke-width="1.4" fill="none"/></svg>Cryotherapy / Cold Compression</li>
    <li><svg viewBox="0 0 10 10"><circle cx="5" cy="5" r="5" fill="var(--tick)"/><path d="M2.8 5.1 4.4 6.6 7.3 3.6" stroke="var(--panel)" stroke-width="1.4" fill="none"/></svg>Acupuncture / Electrical Therapy</li>
    <li><svg viewBox="0 0 10 10"><circle cx="5" cy="5" r="5" fill="var(--tick)"/><path d="M2.8 5.1 4.4 6.6 7.3 3.6" stroke="var(--panel)" stroke-width="1.4" fill="none"/></svg>Home based exercise options</li>
    <li><svg viewBox="0 0 10 10"><circle cx="5" cy="5" r="5" fill="var(--tick)"/><path d="M2.8 5.1 4.4 6.6 7.3 3.6" stroke="var(--panel)" stroke-width="1.4" fill="none"/></svg>Topical Supplements</li>
    <li><svg viewBox="0 0 10 10"><circle cx="5" cy="5" r="5" fill="var(--tick)"/><path d="M2.8 5.1 4.4 6.6 7.3 3.6" stroke="var(--panel)" stroke-width="1.4" fill="none"/></svg>Nonsurgical Options</li>
    <li><svg viewBox="0 0 10 10"><circle cx="5" cy="5" r="5" fill="var(--tick)"/><path d="M2.8 5.1 4.4 6.6 7.3 3.6" stroke="var(--panel)" stroke-width="1.4" fill="none"/></svg>Customized Bracing</li>
    <li><svg viewBox="0 0 10 10"><circle cx="5" cy="5" r="5" fill="var(--tick)"/><path d="M2.8 5.1 4.4 6.6 7.3 3.6" stroke="var(--panel)" stroke-width="1.4" fill="none"/></svg>Topical Medications</li>
    <li><svg viewBox="0 0 10 10"><circle cx="5" cy="5" r="5" fill="var(--tick)"/><path d="M2.8 5.1 4.4 6.6 7.3 3.6" stroke="var(--panel)" stroke-width="1.4" fill="none"/></svg>Exercise Protocols</li>
    <li><svg viewBox="0 0 10 10"><circle cx="5" cy="5" r="5" fill="var(--tick)"/><path d="M2.8 5.1 4.4 6.6 7.3 3.6" stroke="var(--panel)" stroke-width="1.4" fill="none"/></svg>Athletic Trainer</li>
    <li><svg viewBox="0 0 10 10"><circle cx="5" cy="5" r="5" fill="var(--tick)"/><path d="M2.8 5.1 4.4 6.6 7.3 3.6" stroke="var(--panel)" stroke-width="1.4" fill="none"/></svg>Exercise Physiologist</li>
  </ul>
  <div class="round-photo round-photo--knee" role="img" aria-label="Hands holding a painful knee highlighted in red"></div>
  <div class="contact">
    <p class="contact__cta">SCHEDULE YOUR APPOINTMENT TODAY</p>
    <div class="contact__row">
      <span class="contact__item"><svg viewBox="0 0 10 10"><circle cx="5" cy="5" r="5" fill="var(--tick)"/><path d="M3 2.6 4.2 2.4 4.7 3.9 4 4.5 5.6 6 6.2 5.4 7.6 6 7.4 7.2C5 7.4 2.7 5 3 2.6Z" fill="var(--panel)"/></svg>555-014-2290</span>
      <span class="contact__item"><svg viewBox="0 0 10 10"><circle cx="5" cy="5" r="5" fill="var(--tick)"/><rect x="3" y="2.4" width="4" height="2" fill="var(--panel)"/><rect x="2.2" y="4.6" width="5.6" height="2.6" fill="var(--panel)"/></svg>555-014-2291</span>
      <span class="contact__item"><svg viewBox="0 0 10 10"><circle cx="5" cy="5" r="5" fill="var(--tick)"/><circle cx="5" cy="5" r="2.8" fill="none" stroke="var(--panel)" stroke-width=".8"/><path d="M2.2 5H7.8M5 2.2C3.6 4 3.6 6 5 7.8M5 2.2C6.4 4 6.4 6 5 7.8" stroke="var(--panel)" stroke-width=".7" fill="none"/></svg>www.rmhknee.example</span>
    </div>
    <div class="contact__row">
      <span class="contact__item"><svg viewBox="0 0 10 10"><circle cx="5" cy="5" r="5" fill="var(--tick)"/><path d="M5 8 3.2 5.2A2 2 0 1 1 6.8 5.2Z" fill="var(--panel)"/><circle cx="5" cy="4.1" r=".8" fill="var(--tick)"/></svg>1180 Harbor Crest Avenue, Lakeside, FL, 30000</span>
    </div>
  </div>
</section>

<!-- Procedures card -->
<section class="rack-card rack-card--procedures">
  <div class="hero-photo hero-photo--clinic" role="img" aria-label="Front entrance of the clinic building under a cloudy blue sky"></div>
  <div class="brand-name"><span class="brand-name__short">RMH</span><span class="brand-name__long">Ridgeline Medical Health</span></div>
  <svg class="wave" viewBox="0 0 323 130" preserveAspectRatio="none" aria-hidden="true">
    <path d="M0,70 C60,50 120,56 190,96 L0,130 Z" fill="var(--panel)"/>
    <path d="M0,100 C70,76 140,96 200,98 C262,100 300,66 323,46 L323,130 L0,130 Z" fill="var(--wave-white)"/>
    <path d="M0,108 C70,88 140,112 205,114 C262,115 300,84 323,62 L323,130 L0,130 Z" fill="var(--wave-grey)"/>
    <path d="M0,114 C70,96 140,102 200,104 C262,104 300,78 323,66 L323,130 L0,130 Z" fill="var(--panel)"/>
  </svg>
  <div class="count-heading">
    <span class="count-heading__number">6</span>
    <h2 class="count-heading__text">PROCEDURES<br>OFFERED:</h2>
  </div>
  <ul class="checklist checklist--procedures">
    <li><svg viewBox="0 0 10 10"><circle cx="5" cy="5" r="5" fill="var(--tick)"/><path d="M2.8 5.1 4.4 6.6 7.3 3.6" stroke="var(--panel)" stroke-width="1.4" fill="none"/></svg>Interarticular Knee Injection</li>
    <li><svg viewBox="0 0 10 10"><circle cx="5" cy="5" r="5" fill="var(--tick)"/><path d="M2.8 5.1 4.4 6.6 7.3 3.6" stroke="var(--panel)" stroke-width="1.4" fill="none"/></svg>Pes Anserine Bursa</li>
    <li><svg viewBox="0 0 10 10"><circle cx="5" cy="5" r="5" fill="var(--tick)"/><path d="M2.8 5.1 4.4 6.6 7.3 3.6" stroke="var(--panel)" stroke-width="1.4" fill="none"/></svg>Genicular Nerve Block</li>
    <li><svg viewBox="0 0 10 10"><circle cx="5" cy="5" r="5" fill="var(--tick)"/><path d="M2.8 5.1 4.4 6.6 7.3 3.6" stroke="var(--panel)" stroke-width="1.4" fill="none"/></svg>Genicular Radiofrequency Ablation</li>
    <li><svg viewBox="0 0 10 10"><circle cx="5" cy="5" r="5" fill="var(--tick)"/><path d="M2.8 5.1 4.4 6.6 7.3 3.6" stroke="var(--panel)" stroke-width="1.4" fill="none"/></svg>HA (hyaluronic acid) Injections</li>
    <li><svg viewBox="0 0 10 10"><circle cx="5" cy="5" r="5" fill="var(--tick)"/><path d="M2.8 5.1 4.4 6.6 7.3 3.6" stroke="var(--panel)" stroke-width="1.4" fill="none"/></svg>Arnivel Injections</li>
  </ul>
  <div class="physician">
    <p class="physician__name">Marcus Ellery, M.D.</p>
    <p class="physician__role">Interventional<br>Pain Management</p>
  </div>
  <div class="round-photo round-photo--doctor" role="img" aria-label="Portrait of the physician standing by a lake"></div>
  <div class="contact">
    <p class="contact__cta">SCHEDULE YOUR APPOINTMENT TODAY</p>
    <div class="contact__row">
      <span class="contact__item"><svg viewBox="0 0 10 10"><circle cx="5" cy="5" r="5" fill="var(--tick)"/><path d="M3 2.6 4.2 2.4 4.7 3.9 4 4.5 5.6 6 6.2 5.4 7.6 6 7.4 7.2C5 7.4 2.7 5 3 2.6Z" fill="var(--panel)"/></svg>555-014-2290</span>
      <span class="contact__item"><svg viewBox="0 0 10 10"><circle cx="5" cy="5" r="5" fill="var(--tick)"/><rect x="3" y="2.4" width="4" height="2" fill="var(--panel)"/><rect x="2.2" y="4.6" width="5.6" height="2.6" fill="var(--panel)"/></svg>555-014-2291</span>
      <span class="contact__item"><svg viewBox="0 0 10 10"><circle cx="5" cy="5" r="5" fill="var(--tick)"/><circle cx="5" cy="5" r="2.8" fill="none" stroke="var(--panel)" stroke-width=".8"/><path d="M2.2 5H7.8M5 2.2C3.6 4 3.6 6 5 7.8M5 2.2C6.4 4 6.4 6 5 7.8" stroke="var(--panel)" stroke-width=".7" fill="none"/></svg>www.rmhknee.example</span>
    </div>
    <div class="contact__row">
      <span class="contact__item"><svg viewBox="0 0 10 10"><circle cx="5" cy="5" r="5" fill="var(--tick)"/><path d="M5 8 3.2 5.2A2 2 0 1 1 6.8 5.2Z" fill="var(--panel)"/><circle cx="5" cy="4.1" r=".8" fill="var(--tick)"/></svg>1180 Harbor Crest Avenue, Lakeside, FL, 30000</span>
    </div>
  </div>
</section>

</body>
</html>
```